Business Card Design Project

We need a business card for a new technology services company. We develop software and implement software packages for our business customers and although we will begin with just one or two service offerings, our service offerings will expand over time. Our name comes from the an author, KL Barrow, and his "idea" was that opportunity should be based on ability and achievement, not on social status.

We would like to see a design that is standard in its size and shape, but stands apart in its dramatic color contrasts. The card should not use too many colors - the colors used in the background should highlight the brilliant blues of the logo (see attachment) to dramatic effect. The background should not be white.

If necessary, you can change the color of the words "KL Barrow", but not the word "Idea".

Card size should be U.S. standard 2 inches by 3.5 inches and provide for 1/8 inch bleed area on each side.

We need a design for both sides of the business card, one side communicating the company logo and contact information, the other side being purely graphical, incorporating the logo but no other information.

Contact Information Required:
Kate Brook
KateBrook@klbarrowvista.com
614-387-2259

Target Market(s)

Business executives

Industry/Entity Type

Software

Requirements
Must have
• It must have the full company logo on one side, and at least the graphic element of the logo on the other. Either that or the full logo on both.
Nice to have
• It would be nice to have a design that could work without needing two different textures. For example, it would be nice if the entire card could be shiny, not just parts of the card.

It would also be nice if texture is something we could add later.
Should not have
• The card should not use the color green.

```html
<!DOCTYPE html>
<html lang="en">
<head>
<meta charset="utf-8">
<title>KLBarrowVista Business Card</title>
<link href="https://fonts.googleapis.com/css2?family=Open+Sans:wght@400;600&display=swap" rel="stylesheet">
<style>
  :root {
    --stage: #404040;
    --sheet: #ffffff;
    --blue-deep: #0077b6;
    --blue-bright: #00aeef;
    --blue-mark: #0a96d6;
    --card-center: #ffffff;
    --card-edge: #cfd0d2;
    --ink: #1e1e1e;
    --ink-soft: #555a5e;
    --ink-muted: #9a9a9a;
  }
  * { margin: 0; padding: 0; box-sizing: border-box; }
  html, body { width: 1200px; height: 900px; overflow: hidden; }
  body {
    background: var(--stage);
    font-family: "Open Sans", Arial, sans-serif;
    position: relative;
  }
  .sheet {
    position: absolute; left: 212px; top: 0;
    width: 776px; height: 900px;
    background: var(--sheet);
  }
  .sheet-banner {
    position: absolute; left: 212px; top: 48px;
    width: 288px; height: 61px;
    background: linear-gradient(90deg, var(--blue-deep), var(--blue-bright));
    color: #fff; font-size: 12.5px;
    padding: 19px 0 0 58px;
    letter-spacing: 0.2px;
  }
  .card {
    position: absolute; top: 290px;
    width: 561px; height: 320px;
    background: radial-gradient(ellipse 62% 70% at 50% 55%, var(--card-center) 20%, var(--card-edge) 100%);
    box-shadow: 2px 3px 5px rgba(0,0,0,0.55);
  }
  .card-front { left: 20px; }
  .card-back { left: 610px; }
  .brand {
    position: absolute; left: 180px; top: 160px;
    display: flex; align-items: center; gap: 14px;
  }
  .brand-name {
    font-size: 23px; font-weight: 400; color: var(--blue-mark);
    letter-spacing: -0.5px;
  }
  .brand-dot {
    width: 34px; height: 34px; border-radius: 50%;
    background: var(--blue-mark);
  }
  .back-mark {
    position: absolute; left: 40px; top: 100px;
    width: 140px; height: 140px; border-radius: 50%;
    background: var(--blue-mark);
  }
  .contact {
    position: absolute; left: 280px; top: 122px;
    border-left: 2px solid var(--blue-mark);
    padding-left: 26px; height: 63px;
  }
  .contact p {
    font-size: 12.5px; line-height: 24px;
    color: var(--ink-soft); letter-spacing: 0.4px;
    text-transform: uppercase; margin-top: -6px;
  }
  .contact p + p { margin-top: 0; }
  .contact .contact-name { color: var(--ink); }
  .sheet-footer {
    position: absolute; left: 401px; top: 821px;
    font-size: 10.5px; color: var(--ink-muted);
    white-space: nowrap;
  }
  .sheet-footer .sep { margin: 0 10px; }
  .sheet-footer .mail { color: var(--ink); font-size: 11.5px; }
  .sheet-footer .mail-domain { color: var(--blue-mark); }
</style>
</head>
<body>
  <div class="sheet"></div>
  <div class="sheet-banner">KLBarrowVista Services</div>

  <section class="card card-front">
    <div class="brand">
      <span class="brand-name">KLBarrowVista</span>
      <span class="brand-dot"></span>
    </div>
  </section>

  <section class="card card-back">
    <div class="back-mark"></div>
    <div class="contact">
      <p class="contact-name">Kate Brook</p>
      <p>KateBrook@klbarrowvista.com</p>
      <p>614-387-2259</p>
    </div>
  </section>

  <footer class="sheet-footer">
    New technology services company&nbsp;&nbsp;614-387-2259<span class="sep">|</span><span class="mail">katebrook<span class="mail-domain">@KLbarrowvista</span>.com</span>
  </footer>
</body>
</html>
```